Velvet Ladle Wishes Website Design; Cupcake Business with a unique and bespoke design element

We need a website design for a new bespoke and unique business making gourmet cupcakes - but MOST IMPORTANTLY we design and handmake cupcake wrappers and toppers specifically for each client's event. We are based in Sydney, Australia. The final resulting website should be elegant yet whimsical reflecting the notion of dreams and very elegant events eg weddings and very special parties.

We want to eventually have about 5 pages, HOWEVER, this project is specifically for the first page (ie Home page) and one other only. The final required pages are: a HOME page; ABOUT US page; PHOTO GALLERY page; FLAVOUR MENU & OTHER PRODUCTS page; CONTACT & INTERNET ENQUIRY page.

We expect the HOME page to be quite elaborate, perhaps including some animation. We will be providing the text content for all the other pages, and basically they will have the same background as the home page. We are looking for a clean design that runs across each page thus giving the website a continuity that pulls it all together. We would like our logo to be included on each page.

PLEASE NOTE: We will want multiple pages worked on in the handover phase but initially we want a very concise, consistent template to limit the amount of work to prospective designers.

While we are primarily looking for the design phase to be covered by this project, we would certainly appreciate coding to be included and will take that into consideration when choosing a winner.
Updates

Hi Designers

We have added some more information to our brief - please review it.

Thanks and happy designing

Hi Designers

Please note that we have increased our Prize money to $750.00.  We hope this encourages you to participate.

Thanks and regards
Velvet Ladle Wishes

Hi Designers

We've just posted some photos to help give you an idea of what we do.  Please note our attention to detail and precision in our work.

Thanks
Velvet Ladle Wishes

Hi Designers

Please Note:  What makes us different  to any other cupcake business is that we design cupcake wrappers and toppers, unique to our client's event whether it be a wedding, a birthday party or product launch.  We consult with our client to understand themes, colours, styles etc.  We then have our designs printed, next they are cut by a specialised computerised cutting machine,  We assemble everything by hand, and usually embellish the wrapper and topper with pearls, crystals, feathers, lace, ribbons or whatever else is appropriate for the event.  All work is totally bespoke, unique and individual.  No other cupcake supplier that we know of goes to these lengths to satisfy their client's dreams.

THE WRAPPER AND TOPPER IS OUR PRIMARY SELLING POINT. 

PLEASE NOTE:- We have uploaded a new photograph which we want to be used as the main photograph on the landing page.

We have removed all previous photographs of cupcakes (except for one that we can't get rid of).

We don't want a picture of a cupcake on the landing page we want the image _D7C3239.jpg to be used for that purpose.

We have also uploaded our logo in a number of file formats as we have had requests from you for these.

Hi designers

we have a crazy busy weekend on and won't be able to make any decisions re our competition until Monday  -  sorry to keep you in suspense, just a couple more days please!

regards
Pam

Target Market(s)

Primarily women - brides, new mothers (Christenings), Event Planners, who place an emphasis on the beauty of a product rather than the cost

Industry/Entity Type

Events

Requirements
Must have
• It must have our Logo (see attached upload) on each page (our logo is a butterfly atop a cupcake resting on a spoon and our motto is "Creating Delicious Works of Art". The colours used are pale pink, blue and chocolate brown and we'd expect these colours to be repeated in the final website.
The website must have a photo gallery which we can access and add to/change as our business grows.
We need a contact page which has an "internet enquiry form".
There should be a "Menu" page describing our cupcake flavours.
The Home page must have a party/event feel to it - definitely making an enquirer want to enter further into the site.
Nice to have
• Our logo is attached below in the "uploads". One idea that we have had is to use the butterfly in the logo but start it as a caterpillar crawling on the screen; as it spins it's cocoon the words "Sweet Dreams Little Caterpillar" would appear on screen; this would incorporate the "Dreams" in our Business Name; then our logo butterfly would hatch. This encapsulates the idea of taking something plain (caterpillar/cupcake) and creating something beautiful (butterfly/OUR cupcake).
However, we are open to other design ideas.
The colours we would like to have are pale pink, blue and chocolate brown in the design.

Some websites we really admire are: www.mirabellhart.com www.ribbonglitterloaf.com.au and www.greetingsoriel.com.au
These websites have a lightness and sense of fantasy to them. They do not convey a corporate image at all, rather they make you want to be at the party.
Should not have
• No "Corporate" style.

Most Important: We already have a website which we are not happy with - that is why we are going through this exercise to replace it. That means we DO NOT want anything along the lines of our current website. We are expecting some fresh ideas for our prize money.

```html
<!DOCTYPE html>
<html lang="en">
<head>
<meta charset="utf-8">
<title>Velvet Ladle Wishes</title>
<link rel="stylesheet" href="https://fonts.googleapis.com/css2?family=Niconne&family=Reenie+Beanie&family=Ubuntu:wght@400;500&family=PT+Sans:wght@400&family=Roboto:wght@400;500&display=swap">
<style>
:root{
  --page-pink:#fddde2;
  --page-pink-light:#fff0f2;
  --footer-pink:#f9b4c8;
  --ribbon-rose:#df4a72;
  --ribbon-rose-dark:#b7335a;
  --cream:#f8f3ec;
  --cream-shade:#e7ddd0;
  --navy:#1f3f66;
  --plum:#6e2f4a;
  --body-text:#7a4a5c;
  --brown:#6a3f2c;
  --line:#f0b8c6;
  --ink:#2a1a1f;
}
*{box-sizing:border-box;margin:0;padding:0}
html,body{width:1103px;height:1200px;overflow:hidden}
body{background:#fff;font-family:"PT Sans",sans-serif;position:relative}
.page{position:relative;width:1103px;height:1200px;overflow:hidden;
  background:linear-gradient(180deg,var(--page-pink) 0,var(--page-pink-light) 130px,var(--page-pink) 265px)}
.header{position:absolute;left:0;top:0;width:1103px;height:300px;z-index:3}
.header svg{position:absolute;left:0;top:0}
.brand{position:absolute;left:414px;top:-19px;width:276px;height:276px;border-radius:50%;
  display:flex;align-items:center;justify-content:center;gap:8px;flex-direction:column}
.brand-dot{width:14px;height:14px;border-radius:50%;background:var(--ribbon-rose)}
.brand-name{font-family:"Ubuntu",sans-serif;font-weight:500;font-size:19px;color:var(--brown);margin-top:20px}
.nav a{position:absolute;font-family:"Ubuntu",sans-serif;font-weight:500;font-size:15px;color:var(--navy);text-decoration:none;white-space:nowrap}
.hero{position:absolute;left:0;top:264px;width:1103px;height:405px;z-index:1;
  background:
   radial-gradient(ellipse 260px 180px at 470px 200px,#d7c2a3 0,transparent 70%),
   radial-gradient(ellipse 220px 200px at 930px 150px,#4a4640 0,transparent 75%),
   radial-gradient(ellipse 200px 200px at 80px 220px,#5a4d45 0,transparent 75%),
   linear-gradient(100deg,#8a6c54 0,#b79b7c 35%,#cbb7a1 55%,#9c8b80 80%,#6a625c 100%)}
.content{position:absolute;left:0;top:669px;width:1103px;height:414px;
  background:radial-gradient(ellipse 520px 180px at 560px 0,#fff6f7 0,var(--page-pink) 80%)}
.welcome{position:absolute;left:126px;top:22px;font-family:"Niconne",cursive;font-size:28px;line-height:34px;color:var(--plum);font-weight:400}
.intro{position:absolute;left:125px;top:68px;width:860px;font-size:12px;line-height:16.5px;color:var(--body-text)}
.intro p{margin-bottom:16.5px}
.divider{position:absolute;left:240px;top:242px;width:590px;height:1px;
  background:linear-gradient(90deg,transparent,var(--line),transparent)}
.divider::after{content:"";position:absolute;left:291px;top:-4px;width:9px;height:9px;border-radius:50%;background:var(--line)}
.script{font-family:"Reenie Beanie",cursive;color:var(--plum);font-weight:400}
.testimonials-title{position:absolute;left:123px;top:258px;font-size:32px;line-height:34px}
.quote{position:absolute;left:128px;top:299px;width:547px;height:50px;border:1px solid #e5a4b6;border-radius:5px;
  background:linear-gradient(180deg,#fff4f6,#fcd3de);padding:8px 8px;font-size:12px;line-height:16.5px;color:var(--body-text)}
.quote::after{content:"";position:absolute;left:478px;bottom:-14px;width:0;height:0;
  border-right:16px solid transparent;border-top:14px solid #e5a4b6}
.quote-author{position:absolute;left:578px;top:366px;font-family:"Roboto",sans-serif;font-weight:500;font-size:12px;color:var(--plum)}
.social{position:absolute;left:734px;top:330px;display:flex;align-items:center;gap:5px}
.social-title{font-size:29px;line-height:28px;margin-right:10px}
.social-icon{width:24px;height:24px;border-radius:3px;display:block}
.social-icon.one{background:#3b5a98}.social-icon.two{background:#3fb7e6}
.social-icon.three{background:#2d7fb6}.social-icon.four{background:#f08a24}
.footer{position:absolute;left:0;top:1083px;width:1103px;height:107px;background:var(--footer-pink)}
.footer-nav{position:absolute;left:119px;top:46px;font-family:"Ubuntu",sans-serif;font-size:11.5px;color:var(--ink)}
.footer-nav a{color:var(--ink);text-decoration:none}
.footer-nav span{margin:0 14px;color:var(--ink)}
.copyright{position:absolute;right:123px;top:30px;font-family:"Roboto",sans-serif;font-size:11.5px;color:var(--ink)}
.call{position:absolute;right:123px;top:47px;font-family:"Roboto",sans-serif;font-weight:500;font-size:22px;color:var(--brown);letter-spacing:.5px}
</style>
</head>
<body>
<div class="page">
  <header class="header">
    <svg width="1103" height="300" viewBox="0 0 1103 300" aria-hidden="true">
      <path d="M228 38 L350 46 L372 86 L248 90 L262 64 Z" fill="var(--ribbon-rose)"/>
      <path d="M348 28 Q400 22 432 40 L432 84 Q400 70 366 84 Z" fill="var(--ribbon-rose-dark)"/>
      <path d="M875 38 L753 46 L731 86 L855 90 L841 64 Z" fill="var(--ribbon-rose)"/>
      <path d="M755 28 Q703 22 671 40 L671 84 Q703 70 737 84 Z" fill="var(--ribbon-rose-dark)"/>
      <path d="M0 228 Q60 210 112 206 L112 282 Q60 285 20 296 L40 262 Z" fill="var(--cream-shade)"/>
      <path d="M1103 228 Q1043 210 991 206 L991 282 Q1043 285 1083 296 L1063 262 Z" fill="var(--cream-shade)"/>
      <path d="M110 186 Q552 140 1000 186 L1000 270 Q552 228 110 272 Z" fill="var(--cream)"/>
      <path d="M110 272 Q552 228 1000 270 L1000 276 Q552 236 110 278 Z" fill="var(--cream-shade)"/>
      <circle cx="552" cy="119" r="140" fill="#fff"/>
      <circle cx="552" cy="119" r="136" fill="#efe8dc"/>
    </svg>
    <div class="brand">
      <span class="brand-dot"></span>
      <span class="brand-name">Velvet Ladle Wishes</span>
    </div>
    <nav class="nav">
      <a href="#" style="left:145px;top:209px;transform:rotate(-6deg)">Home</a>
      <a href="#" style="left:245px;top:194px;transform:rotate(-3deg)">About Us</a>
      <a href="#" style="left:366px;top:190px;transform:rotate(-1deg)">Products</a>
      <a href="#" style="left:681px;top:190px;transform:rotate(1deg)">Menu</a>
      <a href="#" style="left:778px;top:198px;transform:rotate(3deg)">Photo Gallery</a>
      <a href="#" style="left:912px;top:211px;transform:rotate(5deg)">Contact</a>
    </nav>
  </header>

  <div class="hero" role="img" aria-label="Photograph of a craft table with paper roses, pearls, crystals, feathers, ribbons, lace and scissors"></div>

  <main class="content">
    <h1 class="welcome">Welcome to Velvet Ladle Wishes</h1>
    <div class="intro">
      <p>Velvet Ladle Wishes is a gourmet cupcake service based in Larkmoor, Sydney, specialising in artistic creations focusing heavily on design, colour, theme and most importantly taste!</p>
      <p>We handcraft the best cupcakes that you have ever tasted and they're beautiful too.&nbsp; Our cupcake toppers and wrappers are designed personally for your event making them a unique work of art that have the WOW factor.&nbsp; It's not just a cupcake &nbsp;-&nbsp; Velvet Ladle Wishes are indulgent, luxurious, chic and delicious.</p>
      <p>We are experts in selecting just the right colours and accents to match your colour palette, theme, or company logo.&nbsp; Everything we do is completely bespoke and we use colour/fabric swatches, floral arrangements, invitations or even just an idea to create a display at your event which will have your guests talking for weeks! We work with you every step of the way to make sure that your cupcakes will not only meet your requirements but exceed your expectations too.</p>
    </div>
    <div class="divider"></div>
    <h2 class="script testimonials-title">Testimonials....</h2>
    <blockquote class="quote">"thank you so much for such an amazing display at Imogen's party ?&nbsp; my Mum is still showing all her friends the photos "</blockquote>
    <p class="quote-author">(Rosalind)</p>
    <div class="social">
      <span class="script social-title">Social Networks</span>
      <a class="social-icon one" href="#" aria-label="Social network one"></a>
      <a class="social-icon two" href="#" aria-label="Social network two"></a>
      <a class="social-icon three" href="#" aria-label="Social network three"></a>
      <a class="social-icon four" href="#" aria-label="News feed"></a>
    </div>
  </main>

  <footer class="footer">
    <nav class="footer-nav">
      <a href="#">Home</a><span>|</span><a href="#">About Us</a><span>|</span><a href="#">Products</a><span>|</span><a href="#">Menu</a><span>|</span><a href="#">Photo Gallery</a><span>|</span><a href="#">Contact</a>
    </nav>
    <p class="copyright">© Copyright Velvet Ladle Wishes 2012</p>
    <p class="call">CALL : 0412 386 507</p>
  </footer>
</div>
</body>
</html>
```